Bookcover: Ways to Turn Into a Bold Pathfinder

I am publishing a super-low-cost innovation book for €4,99 on Quillmere Open Press to help everyone become a great innovator: young ambitious people without college education nor a big budget. Do you want to help me?

Brief:
Design a book cover 1600 x 2560 pixels for QOP.
Main title: Ways to Turn Into a Bold Pathfinder
Sub title: mindset - insights - skills & tools
Author: Joost ter Brakel
Design: captive, and appealing to everyone
Target Group: young ambitious people without college education

For quillmere please format the height/width ratio of 1.6:1

```html
<!DOCTYPE html>
<html lang="en">
<head>
<meta charset="UTF-8">
<title>Ways to Turn Into a Bold Pathfinder — Book Cover</title>
<link href="https://fonts.googleapis.com/css2?family=Bebas+Neue&family=Oswald:wght@200;600&family=Poppins:wght@800&family=Great+Vibes&display=swap" rel="stylesheet">
<style>
  :root {
    --night: #03050e;
    --yellow-bright: #f8fb10;
    --yellow-deep: #e9c10c;
    --white: #ffffff;
    --glow-core: #ffb23a;
    --glow-mid: #8a4a12;
  }
  * { margin: 0; padding: 0; box-sizing: border-box; }
  html, body { width: 724px; height: 1200px; overflow: hidden; background: var(--night); }
  .cover {
    position: relative;
    width: 724px;
    height: 1200px;
    background: var(--night);
    overflow: hidden;
  }
  .title-lead {
    position: absolute;
    top: 56px; left: 0; width: 100%;
    text-align: center;
    font-family: "Great Vibes", cursive;
    font-size: 86px;
    color: var(--white);
    line-height: 1;
  }
  .two-tone {
    background: linear-gradient(to bottom, var(--yellow-bright) 0 52%, var(--yellow-deep) 52% 100%);
    -webkit-background-clip: text;
    background-clip: text;
    color: transparent;
  }
  .title-verb {
    position: absolute;
    top: 140px; left: 0; width: 100%;
    text-align: center;
    font-family: "Bebas Neue", sans-serif;
    font-size: 146px;
    line-height: 1;
    letter-spacing: 4px;
  }
  .title-verb span { display: inline-block; }
  .title-bridge {
    position: absolute;
    top: 274px; left: 0; width: 100%;
    display: flex; align-items: center; justify-content: center;
  }
  .rule { width: 158px; height: 2px; background: var(--yellow-bright); margin-top: 40px; }
  .bridge-text {
    font-family: "Bebas Neue", sans-serif;
    font-size: 64px;
    line-height: 1;
    color: var(--white);
    letter-spacing: 20px;
    margin: 0 16px 0 36px;
  }
  .title-noun {
    position: absolute;
    top: 330px; left: 0; width: 100%;
    text-align: center;
    font-family: "Bebas Neue", sans-serif;
    font-size: 184px;
    line-height: 1;
    letter-spacing: -1px;
  }
  .title-noun span { display: inline-block; }
  .bulb-art {
    position: absolute;
    left: 300px; top: 500px;
    width: 380px; height: 650px;
    background:
      radial-gradient(ellipse 38% 26% at 50% 38%, var(--glow-core) 0%, #d7701d 35%, var(--glow-mid) 65%, transparent 100%),
      radial-gradient(ellipse 50% 42% at 50% 42%, rgba(120,70,25,0.35) 0%, transparent 100%);
  }
  .pillars {
    position: absolute;
    left: 61px; top: 540px;
    list-style: none;
  }
  .pillars li {
    font-size: 84px;
    line-height: 76px;
    letter-spacing: -1px;
  }
  .pillars .thin { font-family: "Oswald", sans-serif; font-weight: 200; color: var(--white); }
  .pillars .bold { font-family: "Oswald", sans-serif; font-weight: 600; color: var(--yellow-bright); letter-spacing: -2px; }
  .author-label {
    position: absolute;
    left: 61px; top: 962px;
    font-family: "Great Vibes", cursive;
    font-size: 58px;
    color: var(--yellow-bright);
    line-height: 1;
  }
  .author-name {
    position: absolute;
    left: 61px; top: 1028px;
    font-family: "Poppins", sans-serif;
    font-weight: 800;
    font-size: 40px;
    line-height: 46px;
    letter-spacing: 6px;
    color: var(--white);
  }
</style>
</head>
<body>
<main class="cover">
  <div class="bulb-art" role="img" aria-label="Photograph of a glowing light bulb with a fiery tangled filament and drifting sparks"></div>

  <h1>
    <span class="title-lead">Ways to</span>
    <span class="title-verb"><span class="two-tone">TURN INTO</span></span>
    <span class="title-bridge"><span class="rule"></span><span class="bridge-text">A BOLD</span><span class="rule"></span></span>
    <span class="title-noun"><span class="two-tone">PATHFINDER</span></span>
  </h1>

  <ul class="pillars">
    <li class="thin">MINDSET</li>
    <li class="thin">INSIGHTS</li>
    <li class="bold">SKILLS &amp;</li>
    <li class="bold">TOOLS</li>
  </ul>

  <p class="author-label">Author</p>
  <p class="author-name">JOOST TER<br>BRAKEL</p>
</main>
</body>
</html>
```